Splash Screen for a new release of software

Our company Tarnwick Asia Pacific writes business management software for the automotive industry. Early next year we are planning on releasing our new version of Velcorin, this is a fourth generation product. Our thoughts are to brand this version simply Velcorin 4, however we do wish to add a certain exclusivity to product hence the addition of Lantern Edition as a signature to the Velcorin brand. The splash screen has to make the user feel that they are using an upmarket product and are excited to be doing so. I have uploaded an "in house" design for reference purposes, also included our sphere company logo.

```html
<!DOCTYPE html>
<html lang="en">
<head>
<meta charset="utf-8">
<title>Velcorin 4 Lantern Edition – Splash Screens</title>
<link rel="stylesheet" href="https://fonts.googleapis.com/css2?family=Montserrat:wght@300;400;800&display=swap">
<style>
  :root {
    --stage-bg: #dde7ee;
    --white: #ffffff;
    --numeral: rgba(255, 255, 255, 0.22);
    --mark-fill: #5a0a3a;
    --dusk-violet: #a48cc4;
    --dusk-rose: #d9c0d2;
    --dusk-peach: #f5d2b0;
    --dusk-shore: #8e6a86;
    --mist-lilac: #cbbfd9;
    --mist-violet: #a99ac0;
    --mist-slate: #7d7390;
    --mist-shore: #6a5c66;
  }
  * { margin: 0; padding: 0; box-sizing: border-box; }
  html, body {
    width: 1200px;
    height: 898px;
    overflow: hidden;
    background: var(--stage-bg);
    font-family: "Montserrat", sans-serif;
  }
  .stage { position: relative; width: 1200px; height: 898px; }
  .splash {
    position: absolute;
    left: 360px;
    width: 480px;
    height: 326px;
    overflow: hidden;
    color: var(--white);
  }
  .splash--dusk { top: 90px; }
  .splash--mist { top: 483px; }
  .splash__photo { position: absolute; inset: 0; }
  .splash--dusk .splash__photo {
    background: linear-gradient(160deg, var(--dusk-violet) 0%, var(--dusk-rose) 40%, var(--dusk-peach) 62%, var(--dusk-shore) 100%);
  }
  .splash--mist .splash__photo {
    background: linear-gradient(180deg, var(--mist-lilac) 0%, var(--mist-violet) 35%, var(--mist-slate) 62%, var(--mist-shore) 100%);
  }
  .splash__title {
    position: absolute;
    left: 8px;
    top: -6px;
    font-weight: 800;
    font-size: 45px;
    letter-spacing: -0.5px;
    line-height: 1.1;
    text-transform: uppercase;
  }
  .splash__edition {
    position: absolute;
    left: 7px;
    top: 38px;
    font-weight: 300;
    font-size: 16.5px;
    letter-spacing: 0.3px;
  }
  .splash__numeral {
    position: absolute;
    left: 180px;
    top: 58px;
    width: 124px;
    text-align: center;
    font-weight: 300;
    font-size: 160px;
    line-height: 1;
    color: var(--numeral);
  }
  .splash__date {
    position: absolute;
    left: 8px;
    bottom: 3px;
    font-size: 10px;
    font-weight: 400;
  }
  .splash__credits {
    position: absolute;
    left: 140px;
    width: 200px;
    bottom: 3px;
    text-align: center;
    font-size: 10px;
    font-weight: 400;
    line-height: 1.15;
  }
  .splash__brand {
    position: absolute;
    right: 18px;
    bottom: 38px;
    display: flex;
    align-items: center;
    gap: 6px;
  }
  .splash__brand-dot {
    width: 28px;
    height: 28px;
    border-radius: 50%;
    background: var(--mark-fill);
  }
  .splash__brand-name {
    font-size: 11px;
    font-weight: 800;
    text-transform: uppercase;
    color: var(--white);
  }
</style>
</head>
<body>
<main class="stage">
  <section class="splash splash--dusk">
    <div class="splash__photo" role="img" aria-label="Long-exposure seascape at dusk: calm violet sea, a low rocky outcrop with moss, peach sky glow on the right"></div>
    <h1 class="splash__title">Velcorin</h1>
    <p class="splash__edition">Lantern Edition</p>
    <div class="splash__numeral" aria-hidden="true">4</div>
    <p class="splash__date">January 21, 2025</p>
    <p class="splash__credits">Version 4.0.0<br>© Tarnwick Asia Pacific Pty Ltd 2016</p>
    <div class="splash__brand"><span class="splash__brand-name">Tarnwick</span><span class="splash__brand-dot"></span></div>
  </section>

  <section class="splash splash--mist">
    <div class="splash__photo" role="img" aria-label="Misty seascape in cool lilac tones: still water and a mossy rocky outcrop near the shore"></div>
    <h1 class="splash__title">Velcorin</h1>
    <p class="splash__edition">Lantern Edition</p>
    <div class="splash__numeral" aria-hidden="true">4</div>
    <p class="splash__date">January 21, 2025</p>
    <p class="splash__credits">Version 4.0.0<br>© Tarnwick Asia Pacific Pty Ltd 2016</p>
    <div class="splash__brand"><span class="splash__brand-name">Tarnwick</span><span class="splash__brand-dot"></span></div>
  </section>
</main>
</body>
</html>
```